Gestaltung von Honigetiketten
Zielgruppe
Ich bin ein Imker, der im eigenen Restaurant seinen Honig ausstellen und verkaufen möchte.
Aufgabenstellung
Ich möchte exklusive und edle Honigetiketten die auffallen. Bevorzugt mit den Farben Gold und Schwarz, siehe meinem bisher gesehenen Favoriten im Anhang.
Nur das Logo selbst (Baum) soll übernommen werden Farbe kann variieren, ebenso die Schrift ist variabel.
Auf die Vorderseite des Honigetiketts soll zu lesen sein:
- Deutscher Honig
- Sommertracht
- 500g
- Logo und Name
Auf der Rückseite des Honigetiketts soll zu finden sein:
- freies Feld für Stempel für Namen und Adresse des Abfüllers
- freies Feld für das Mindesthaltbarkeitsdatum

```html
<!DOCTYPE html>
<html lang="de">
<head>
<meta charset="utf-8">
<title>Honigetikett Sommertracht</title>
<link rel="stylesheet" href="https://fonts.googleapis.com/css2?family=Fira+Sans+Extra+Condensed&family=Open+Sans&family=Great+Vibes&family=Poiret+One&display=swap">
<style>
  :root {
    --orange-top: #f08a18;
    --orange-mid: #eeae2c;
    --orange-low: #f29012;
    --black: #000000;
    --gold: #d9cc80;
    --gold-light: #ece6b4;
    --gold-dark: #a88a3a;
    --ink: #111111;
  }
  * { margin: 0; padding: 0; box-sizing: border-box; }
  html, body { width: 1006px; height: 1200px; overflow: hidden; }
  body { background: var(--orange-mid); }
  .label {
    position: relative;
    width: 1006px; height: 1200px; overflow: hidden;
    background: linear-gradient(180deg, var(--orange-top) 0%, var(--orange-mid) 58%, var(--orange-mid) 70%, var(--orange-low) 100%);
  }
  .back-strip {
    position: absolute; left: 390px; top: 0; width: 231px; height: 673px;
    background: var(--black);
    box-shadow: 0 6px 14px rgba(0,0,0,0.25);
  }
  .best-before {
    position: absolute; left: 37px; top: 18px; width: 166px; height: 76px;
    background: #fff;
  }
  .best-before span {
    position: absolute; left: 0; right: 0; top: 6px;
    text-align: center; transform: rotate(180deg); white-space: nowrap;
    font: 15px "Fira Sans Extra Condensed", sans-serif; color: var(--ink);
  }
  .brand-mark { position: absolute; left: 35px; top: 277px; }
  .brand-name {
    position: absolute; left: 0; right: 0; top: 454px;
    text-align: center; color: var(--gold);
    font: 25px/27px "Open Sans", sans-serif;
  }
  .gold-band {
    position: absolute; left: 0; top: 685px; width: 1006px; height: 10px;
    background: linear-gradient(90deg, #b89a48 0%, #c0a24c 40%, var(--gold-light) 48%, #e6e09a 58%, #d6cfa0 70%, #d8d2aa 100%);
  }
  .info {
    position: absolute; color: var(--ink); white-space: nowrap;
    font: 22px/30.5px "Fira Sans Extra Condensed", sans-serif;
    letter-spacing: -0.3px; font-style: normal;
  }
  .info-address { left: 14px; top: 704px; }
  .info-storage { left: 735px; top: 711px; line-height: 27px; letter-spacing: -0.5px; }
  .fill-weight {
    position: absolute; left: 735px; top: 827px; white-space: nowrap;
    font: 24px "Open Sans", sans-serif; color: var(--ink);
  }
  .comb { position: absolute; left: 0; top: 0; }
  .seal { position: absolute; left: 343px; top: 708px; }
</style>
</head>
<body>
<main class="label">

  <section class="back-strip">
    <div class="best-before"><span>Mindestens haltbar bis</span></div>
    <svg class="brand-mark" width="162" height="162" viewBox="0 0 162 162" aria-hidden="true">
      <circle cx="81" cy="81" r="79" fill="none" stroke="var(--gold)" stroke-width="2"/>
    </svg>
    <p class="brand-name">Gasthof am Ahorn<br>Brunnsaal</p>
  </section>

  <div class="gold-band"></div>

  <address class="info info-address">
    Gasthaus Am Ahorn-Brunnsaal<br>
    Birkenfelder Straße 12<br>
    91234 Talbach-Erlen<br>
    www.brunnsaal-ahornwirt.de
  </address>

  <p class="info info-storage">
    Lagerhinweis:<br>
    Kühl, dunkel und trocken lagern.<br>
    Mehrwegglas:<br>
    Bitte zurück zum Imker
  </p>
  <p class="fill-weight">Füllmenge 500 g</p>

  <svg class="comb" width="1006" height="1200" viewBox="0 0 1006 1200" role="img" aria-label="Goldenes Wabenmuster">
    <defs>
      <linearGradient id="combLeft" x1="0" y1="0" x2="1" y2="0.2">
        <stop offset="0" stop-color="#b89c4c"/>
        <stop offset="0.4" stop-color="#e6e0b4"/>
        <stop offset="0.65" stop-color="#e2dcae"/>
        <stop offset="1" stop-color="#9c7c30"/>
      </linearGradient>
      <linearGradient id="combRight" x1="0" y1="0.2" x2="1" y2="0">
        <stop offset="0" stop-color="#9c7c30"/>
        <stop offset="0.3" stop-color="#c8b060"/>
        <stop offset="0.65" stop-color="#e6e29c"/>
        <stop offset="1" stop-color="#dcd6ac"/>
      </linearGradient>
    </defs>
    <path d="M0,865 L184,865 L184,937 L302,937 L302,1009 L422,1009 L422,1081 L462,1081 L462,1200 L0,1200 Z" fill="url(#combLeft)"/>
    <path d="M825,865 L1006,865 L1006,1200 L550,1200 L550,1081 L590,1081 L590,1009 L708,1009 L708,937 L825,937 Z" fill="url(#combRight)"/>
  </svg>

  <svg class="seal" width="328" height="328" viewBox="0 0 328 328" aria-label="Sommertracht – Deutscher Honig">
    <defs>
      <linearGradient id="goldText" x1="0" y1="0" x2="1" y2="0">
        <stop offset="0" stop-color="#b89a48"/>
        <stop offset="0.5" stop-color="#ece6b4"/>
        <stop offset="1" stop-color="#c8b060"/>
      </linearGradient>
    </defs>
    <circle cx="164" cy="164" r="162" fill="var(--black)"/>
    <circle cx="164" cy="164" r="157" fill="none" stroke="var(--orange-low)" stroke-width="2.5"/>
    <text x="164" y="131" text-anchor="middle" font-family="'Great Vibes', cursive" font-size="52" fill="url(#goldText)">Sommertracht</text>
    <line x1="26" y1="166" x2="300" y2="166" stroke="url(#goldText)" stroke-width="3"/>
    <text x="164" y="206" text-anchor="middle" font-family="'Poiret One', sans-serif" font-size="32" fill="var(--gold)">Deutscher Honig</text>
  </svg>

</main>
</body>
</html>
```